Business Card for a Dental Office

The design should communicate integrity, quality and reliability. We also want the card look elegant, simple, but still stand out, different from the traditional-dental-office business card.

Industry/Entity Type

Business

```html
<!DOCTYPE html>
<html lang="en">
<head>
<meta charset="utf-8">
<title>Harlow Dental Studio – Business Card</title>
<link rel="stylesheet" href="https://fonts.googleapis.com/css2?family=Open+Sans:wght@400;600;700;800&display=swap">
<style>
  :root {
    --backdrop: #d9d9d9;
    --panel-dark: #3a3a3c;
    --panel-light: #ffffff;
    --accent-gold: #d8c419;
    --text-light: #ffffff;
    --text-dark: #161616;
  }
  * { margin: 0; padding: 0; box-sizing: border-box; }
  html, body {
    width: 1200px;
    height: 977px;
    overflow: hidden;
    background: var(--backdrop);
    font-family: "Open Sans", sans-serif;
  }
  .business-card {
    position: absolute;
    left: 100px;
    top: 203px;
    width: 1000px;
    height: 571px;
    background: var(--panel-light);
    box-shadow: 0 6px 24px rgba(0,0,0,0.18);
    overflow: hidden;
  }
  .card-panels {
    position: absolute;
    inset: 0;
  }
  .contact-side {
    position: absolute;
    left: 110px;
    top: 150px;
    color: var(--text-light);
  }
  .person-name {
    font-size: 44px;
    font-weight: 600;
    color: var(--accent-gold);
    line-height: 1.1;
  }
  .person-role {
    font-size: 22px;
    font-weight: 700;
    margin-left: 14px;
    margin-bottom: 34px;
  }
  .contact-list {
    list-style: none;
    margin-left: 40px;
  }
  .contact-item {
    display: flex;
    align-items: flex-start;
    gap: 16px;
    font-size: 22px;
    line-height: 1.35;
    margin-bottom: 4px;
  }
  .contact-item.address { margin-bottom: 26px; }
  .contact-icon {
    flex: none;
    width: 22px;
    height: 22px;
    margin-top: 5px;
    fill: var(--accent-gold);
  }
  .brand-side {
    position: absolute;
    left: 530px;
    top: 0;
    width: 470px;
    height: 571px;
    display: flex;
    align-items: center;
    justify-content: center;
    gap: 14px;
  }
  .brand-mark {
    width: 42px;
    height: 42px;
    background: var(--accent-gold);
  }
  .brand-name {
    font-size: 34px;
    font-weight: 800;
    color: var(--text-dark);
    letter-spacing: -0.5px;
    text-transform: uppercase;
  }
</style>
</head>
<body>
  <div class="business-card">
    <svg class="card-panels" width="1000" height="571" viewBox="0 0 1000 571" aria-hidden="true">
      <polygon points="0,0 505,0 535,571 0,571" fill="var(--panel-dark)"/>
      <line x1="507" y1="0" x2="537" y2="571" stroke="var(--accent-gold)" stroke-width="4"/>
    </svg>

    <div class="contact-side">
      <div class="person-name">Daniel Reyes</div>
      <div class="person-role">Manager</div>
      <ul class="contact-list">
        <li class="contact-item address">
          <svg class="contact-icon" viewBox="0 0 24 24"><path d="M12 2a7 7 0 0 0-7 7c0 5 7 13 7 13s7-8 7-13a7 7 0 0 0-7-7zm0 9.5A2.5 2.5 0 1 1 12 6.5a2.5 2.5 0 0 1 0 5z"/></svg>
          <span>482 Alder Street,<br>CA 94110</span>
        </li>
        <li class="contact-item">
          <svg class="contact-icon" viewBox="0 0 24 24"><path d="M6.6 10.8a15 15 0 0 0 6.6 6.6l2.2-2.2a1 1 0 0 1 1-.25 11.4 11.4 0 0 0 3.6.57 1 1 0 0 1 1 1V20a1 1 0 0 1-1 1A17 17 0 0 1 3 4a1 1 0 0 1 1-1h3.5a1 1 0 0 1 1 1c0 1.25.2 2.45.57 3.57a1 1 0 0 1-.25 1z"/></svg>
          <span>(555) 218-4073</span>
        </li>
        <li class="contact-item">
          <svg class="contact-icon" viewBox="0 0 24 24"><path d="M2 5h20v14H2z M2 5l10 7 10-7" fill="var(--accent-gold)"/><path d="M2 5l10 7 10-7" fill="none" stroke="var(--panel-dark)" stroke-width="1.6"/></svg>
          <span>hello@harlowdental.com</span>
        </li>
        <li class="contact-item">
          <svg class="contact-icon" viewBox="0 0 24 24"><circle cx="12" cy="12" r="10"/><path d="M2 12h20M12 2c3 3 3 17 0 20M12 2c-3 3-3 17 0 20" fill="none" stroke="var(--panel-dark)" stroke-width="1.4"/></svg>
          <span>www.harlowdental.com</span>
        </li>
      </ul>
    </div>

    <div class="brand-side">
      <div class="brand-mark"></div>
      <div class="brand-name">Harlow Dental Studio</div>
    </div>
  </div>
</body>
</html>
```